New Dynamic Design Based on Other Site

We need a new website designed where the front page is VERY SEO Friendly. The front page should almost follow the same SEO principles that are on RankLoomPress.com. The inner pages need to follow the same exact video animations that occur on vollq.com. I'd like to keep our "marbletons" theme throughout the new design but we will provide all of the content but I want someone to design something SEO friendly, new blog theme, and actual inner pages that are dynamic and based on those short videos.

Check attached file for company name and site that we currently have. Feel free to pull the content from that site and re-use it and also leave placeholders for the rest of them.

PLEASE NO USE OF STOCK IMAGES. Use a designer or an illustrator to create the various images.

Please make sure the front page is SEO friendly! Make sure you familiarize yourself with the quorvix algorithm for SEO. Content above the fold H1 Tags Very mobile friendly Minimal javascript and animations Basically a quality static page with optimized content

Target Market(s)

call center companies, anything call related

Industry/Entity Type

Telecommunications

Number of Pages Required

4 page

Font styles to use
Sans Serif

Colors
33a6d7
85cae6
0792cd
0255a3
cee9f5
ecf7fb
ffffff

Requirements
Must have
• places for video animations
• dynamic functionality
• SEO friendly (front page)
Should not have
• should not look like a template. needs to be unique

```html
<!DOCTYPE html>
<html lang="en">
<head>
<meta charset="utf-8">
<title>Tallymark — Call Center Quality Assurance</title>
<link href="https://fonts.googleapis.com/css2?family=Open+Sans:wght@400;600;700&family=Roboto+Condensed:wght@300;400;700&display=swap" rel="stylesheet">
<style>
:root{
  --sky:#33a6d7;
  --sky-soft:#85cae6;
  --ocean:#0792cd;
  --navy:#0255a3;
  --ice:#cee9f5;
  --mist:#ecf7fb;
  --white:#ffffff;
  --ink:#333b44;
  --muted:#7a838c;
  --panel:#f4f4f4;
  --line:#e3e6e8;
}
*{box-sizing:border-box;margin:0;padding:0}
html,body{width:1200px;height:3550px;overflow:hidden}
body{font-family:"Open Sans",sans-serif;color:var(--ink);background:var(--white);position:relative}
.heading-font{font-family:"Roboto Condensed",sans-serif}
a{color:inherit;text-decoration:none}
.wrap{position:absolute;left:132px;width:936px}

/* top bar */
.topbar{position:absolute;top:0;left:0;width:1200px;height:28px;background:var(--navy);color:var(--white);font-size:11px}
.topbar span{position:absolute;top:7px;display:flex;align-items:center;gap:6px}
/* header */
.site-header{position:absolute;top:28px;left:0;width:1200px;height:102px;background:var(--white)}
.brand{position:absolute;display:flex;align-items:center;gap:10px;font-family:"Open Sans",sans-serif;font-weight:700;color:var(--navy)}
.brand .dot{border-radius:50%;background:var(--ocean)}
.site-header .brand{left:132px;top:26px;font-size:30px}
.site-header .brand .dot{width:40px;height:40px}
.main-nav{position:absolute;top:42px;left:430px;display:flex;gap:0;font-family:"Roboto Condensed",sans-serif;font-size:14px;color:#555}
.main-nav a{position:absolute;white-space:nowrap}
.main-nav .active{color:var(--ocean)}
.login{position:absolute;left:988px;top:30px;width:80px;height:36px;background:var(--ocean);color:var(--white);font-family:"Roboto Condensed",sans-serif;font-size:13px;font-weight:700;display:flex;align-items:center;justify-content:center;gap:6px}

/* hero */
.hero{position:absolute;top:130px;left:0;width:1200px;height:450px;background:linear-gradient(90deg,#4fb9e3,#6fc7ea)}
.hero-art{position:absolute;left:568px;top:0;width:510px;height:450px;background:linear-gradient(180deg,#8dd3ee 0%,#6cc5ea 60%,#4a9ec4 100%);opacity:.85}
.hero-kicker{position:absolute;left:132px;top:92px;font-family:"Roboto Condensed",sans-serif;font-size:24px;font-weight:300;color:var(--white)}
.hero h1{position:absolute;left:132px;top:130px;font-family:"Roboto Condensed",sans-serif;font-size:46px;font-weight:700;color:var(--white);letter-spacing:.5px}
.hero p{position:absolute;left:132px;top:208px;width:400px;font-size:12px;line-height:24px;color:var(--white)}
.btn{display:inline-flex;align-items:center;justify-content:center;font-family:"Roboto Condensed",sans-serif;font-weight:700;font-size:13px;color:var(--white);background:var(--navy)}
.hero .btn{position:absolute;left:132px;top:324px;width:140px;height:34px;background:var(--navy)}
.dots{position:absolute;left:556px;top:404px;display:flex;gap:8px}
.dots i{width:12px;height:12px;border-radius:50%;border:2px solid var(--white)}
.dots i.on{background:var(--white)}

/* intro */
.intro{position:absolute;top:580px;left:0;width:1200px;height:580px;border-bottom:1px solid var(--line)}
.section-title{position:absolute;left:0;width:1200px;text-align:center;font-family:"Roboto Condensed",sans-serif;font-weight:400;font-size:28px;color:#2f3740;text-transform:uppercase}
.intro .section-title{top:92px}
.intro-art{position:absolute;left:132px;top:168px;width:390px;height:330px;background:linear-gradient(180deg,#e9ecef,#cfd5da);border-radius:6px}
.intro-copy{position:absolute;left:606px;top:184px;width:462px}
.intro-copy h2{font-family:"Roboto Condensed",sans-serif;font-weight:400;font-size:17px;color:var(--sky);margin-bottom:14px}
.intro-copy p{font-size:11.5px;line-height:21px;color:var(--muted);margin-bottom:20px}
.intro-copy .btn{margin-top:20px;width:122px;height:36px;background:var(--ocean)}

/* services */
.services{position:absolute;top:1160px;left:0;width:1200px;height:533px}
.services .section-title{top:76px}
.service-grid{position:absolute;left:132px;top:162px;width:960px;display:grid;grid-template-columns:repeat(3,325px);row-gap:52px}
.service{display:flex;gap:16px}
.service .icon{flex:none;width:66px;height:66px;border-radius:50%;display:flex;align-items:center;justify-content:center}
.service h3{font-family:"Open Sans",sans-serif;font-weight:400;font-size:14px;margin:4px 0 6px}
.service p{font-size:10.5px;line-height:17px;color:var(--muted);width:210px}
.service a{display:block;margin-top:6px;font-size:10.5px;color:var(--ocean)}
.c-sky{background:var(--sky)}.c-lime{background:#8cc63f}.c-orange{background:#f7941d}
.c-navy{background:#1f5f9c}.c-teal{background:#1b8fbf}.c-red{background:#ef5a3c}

/* features */
.features{position:absolute;top:1693px;left:0;width:1200px;height:592px;background:var(--panel)}
.features .section-title{top:96px}
.feature-row{position:absolute;left:132px;top:151px;width:936px;height:274px;display:grid;grid-template-columns:repeat(4,1fr)}
.feature{position:relative}
.feature .caption{position:absolute;left:0;bottom:0;width:100%;height:44px;background:rgba(0,0,0,.18);color:var(--white);font-size:13px;display:flex;align-items:center;justify-content:center;gap:6px}
.f1{background:linear-gradient(160deg,#2bb3a3,#1a9d8f)}
.f2{background:linear-gradient(160deg,#73ad79,#5a9864)}
.f3{background:linear-gradient(160deg,#5da6b2,#3f8a9b)}
.f4{background:linear-gradient(160deg,#34c09b,#1faa83)}
.feature-actions{position:absolute;top:459px;left:0;width:1200px;display:flex;justify-content:center;gap:8px}
.feature-actions .btn{height:34px;padding:0 14px;font-size:11.5px;gap:6px}
.feature-actions .alt{background:var(--ocean)}

/* team */
.team{position:absolute;top:2285px;left:0;width:1200px;height:503px;background:var(--ocean);color:var(--white)}
.team .section-title{top:88px;color:var(--white)}
.team-intro{position:absolute;left:170px;top:140px;width:860px;text-align:center;font-size:11.5px;line-height:20px}
.member{position:absolute;top:240px;width:180px;text-align:center}
.member .avatar{width:132px;height:132px;border-radius:50%;margin:0 auto 16px;border:5px solid var(--white);background:radial-gradient(circle at 50% 45%,#f3d35a,#d7b23c 60%,#fff 62%)}
.member h4{font-family:"Roboto Condensed",sans-serif;font-size:13px;font-weight:700;text-transform:uppercase}
.member span{font-size:11px}
.team .arrow{position:absolute;top:255px}

/* press */
.press{position:absolute;top:2788px;left:0;width:1200px;height:202px}
.press-row{position:absolute;left:132px;width:936px;display:grid;grid-template-columns:repeat(8,1fr);text-align:center;font-family:"Open Sans",sans-serif;font-weight:700;font-size:15px;color:#9aa1a7}
.press-row.one{top:62px}.press-row.two{top:116px}

/* testimonial */
.testimonial{position:absolute;top:2990px;left:0;width:1200px;height:276px;background:var(--navy);color:var(--white)}
.testimonial .avatar{position:absolute;left:132px;top:66px;width:120px;height:120px;border-radius:50%;border:5px solid var(--white);background:radial-gradient(circle at 50% 45%,#f3d35a,#d7b23c 60%,#fff 62%)}
.testimonial blockquote{position:absolute;left:300px;top:80px;width:770px;font-size:14px;line-height:24px;font-style:italic}
.testimonial .who{position:absolute;left:300px;top:172px;font-family:"Roboto Condensed",sans-serif;font-weight:700;font-size:14px}
.testimonial .org{position:absolute;left:300px;top:196px;font-size:12px;font-style:italic}
.testimonial .dots{left:1020px;top:200px;gap:4px}
.testimonial .dots i{width:11px;height:11px}

/* footer */
.site-footer{position:absolute;top:3266px;left:0;width:1200px;height:226px;background:var(--white)}
.site-footer .brand{left:132px;top:76px;font-size:32px}
.site-footer .brand .dot{width:44px;height:44px}
.footer-col{position:absolute;top:50px}
.footer-col h5{font-family:"Roboto Condensed",sans-serif;font-weight:400;font-size:16px;text-transform:uppercase;margin-bottom:14px;color:#2f3740}
.footer-col li{list-style:none;font-size:11px;line-height:24px;color:#555;display:flex;align-items:center;gap:8px}
.newsletter input{display:block;width:216px;height:36px;border:0;background:#e9ebed;padding:0 12px;font-family:"Open Sans",sans-serif;font-size:11px;color:#777}
.newsletter .btn{margin-top:12px;width:88px;height:34px;background:var(--ocean);font-size:11.5px}

/* copyright */
.copyright{position:absolute;top:3492px;left:0;width:1200px;height:58px;border-top:1px solid var(--line);font-size:11px;color:#666}
.copyright .left{position:absolute;left:132px;top:20px}
.copyright .right{position:absolute;left:860px;top:14px;display:flex;align-items:center;gap:6px}
.copyright .right i{width:24px;height:24px;border-radius:50%;border:1px solid #c9ced2}
</style>
</head>
<body>

<div class="topbar">
  <span style="left:742px"><svg width="10" height="10" viewBox="0 0 24 24"><path fill="#fff" d="M6.6 10.8a15 15 0 0 0 6.6 6.6l2.2-2.2c.3-.3.7-.4 1-.2 1.1.4 2.3.6 3.6.6.6 0 1 .4 1 1V20c0 .6-.4 1-1 1A17 17 0 0 1 3 4c0-.6.4-1 1-1h3.5c.6 0 1 .4 1 1 0 1.3.2 2.5.6 3.6.1.3 0 .7-.2 1z"/></svg>PHONE: 555.014.2260</span>
  <span style="left:890px"><svg width="11" height="9" viewBox="0 0 24 18"><rect x="1" y="1" width="22" height="16" fill="none" stroke="#fff" stroke-width="2"/><path d="M1 1l11 9 11-9" fill="none" stroke="#fff" stroke-width="2"/></svg>EMAIL: hello@tallymark.com</span>
</div>

<header class="site-header">
  <a class="brand"><span class="dot"></span>Tallymark</a>
  <nav class="main-nav">
    <a class="active" style="left:0">HOME</a>
    <a style="left:100px">WHO WE ARE</a>
    <a style="left:234px">SERVICES</a>
    <a style="left:352px">BLOG</a>
    <a style="left:444px">CONTACT</a>
  </nav>
  <a class="login"><svg width="10" height="11" viewBox="0 0 20 22"><rect x="2" y="9" width="16" height="12" fill="#fff"/><path d="M5 9V6a5 5 0 0 1 10 0v3" fill="none" stroke="#fff" stroke-width="2.5"/></svg>LOG IN</a>
</header>

<section class="hero">
  <div class="hero-art" role="img" aria-label="Illustration of a quality analyst working at a desk with a laptop, shelves and floating chat icons"></div>
  <div class="hero-kicker">WE ARE A CALL CENTER</div>
  <h1>QUALITY ASSURANCE</h1>
  <p>We listen to every call so your team can focus on the customer, with clear scores, honest feedback and simple reports delivered each week.</p>
  <a class="btn">GET STARTED TODAY</a>
  <div class="dots"><i></i><i></i><i class="on"></i><i></i></div>
</section>

<section class="intro">
  <h2 class="section-title">Top Rated Call Center Quality Assurance Agency</h2>
  <div class="intro-art" role="img" aria-label="Illustration of a desktop monitor showing a group of business team members"></div>
  <div class="intro-copy">
    <h2>BECAUSE WE CARE ABOUT OUR PEOPLE AND YOURS!</h2>
    <p>So why use Tallymark's call center quality assurance services to evaluate your customer to agent interactions? If you've ever counted on a voice assistant to look up the nearest Thai restaurant or identify the fastest route to the supermarket,</p>
    <p>You already know that voice recognition software is years away from being as accurate as we would like it to be. Although this provides cheap entertainment for menial tasks, your business's reputation is no laughing matter.</p>
    <a class="btn">READ MORE INFO</a>
  </div>
</section>

<section class="services">
  <h2 class="section-title">Call Center QA Services</h2>
  <div class="service-grid">
    <div class="service"><div class="icon c-sky"><svg width="30" height="30" viewBox="0 0 24 24" fill="none" stroke="#fff" stroke-width="1.8"><path d="M4 14v-2a8 8 0 0 1 16 0v2"/><rect x="3" y="13" width="4" height="6" rx="1"/><rect x="17" y="13" width="4" height="6" rx="1"/></svg></div>
      <div><h3>Call Center Quality Control</h3><p>Boost your revenue and improve customer experience by identifying key behaviors and procedures...</p><a>Read More »</a></div></div>
    <div class="service"><div class="icon c-lime"><svg width="30" height="30" viewBox="0 0 24 24" fill="none" stroke="#fff" stroke-width="1.8"><path d="M4 20h16"/><path d="M6 17v-3M10 17v-6M14 17v-4M18 17V8"/><path d="M5 10l5-4 4 3 5-5"/></svg></div>
      <div><h3>Performance Analysis</h3><p>Are your agents interacting with your clients in a way that is reflective of your brand identity? Effective agent...</p><a>Read More »</a></div></div>
    <div class="service"><div class="icon c-orange"><svg width="30" height="30" viewBox="0 0 24 24" fill="none" stroke="#fff" stroke-width="1.8"><rect x="3" y="7" width="18" height="13" rx="1"/><path d="M9 7V4h6v3"/></svg></div>
      <div><h3>Business Process Verification</h3><p>Because higher quality touch points lead to loyal customers, and loyal customers result in repeat purchase...</p><a>Read More »</a></div></div>
    <div class="service"><div class="icon c-navy"><svg width="30" height="30" viewBox="0 0 24 24" fill="none" stroke="#fff" stroke-width="1.8"><circle cx="12" cy="12" r="9"/><path d="M9.5 9.5a2.5 2.5 0 1 1 3.5 2.3c-.7.3-1 .9-1 1.7"/><circle cx="12" cy="17" r=".6" fill="#fff"/></svg></div>
      <div><h3>Call Center Compliance</h3><p>At Tallymark, we make compliance easy. To alleviate the risk of non-compliance in customer - agent interactions...</p><a>Read More »</a></div></div>
    <div class="service"><div class="icon c-teal"><svg width="30" height="30" viewBox="0 0 24 24" fill="none" stroke="#fff" stroke-width="1.8"><circle cx="12" cy="12" r="9"/><path d="M3 12h18M12 3c3 3 3 15 0 18M12 3c-3 3-3 15 0 18"/></svg></div>
      <div><h3>Call Center Affiliate</h3><p>Did you know that selecting the right partner is one of the most crucial foundational elements for creating...</p><a>Read More »</a></div></div>
    <div class="service"><div class="icon c-red"><svg width="30" height="30" viewBox="0 0 24 24" fill="none" stroke="#fff" stroke-width="1.8"><path d="M12 3l8 3v6c0 5-4 8-8 9-4-1-8-4-8-9V6z"/><path d="M8.5 12l2.5 2.5 4.5-5"/></svg></div>
      <div><h3>TCPA Verification</h3><p>While the legal landscape around the Telephone Consumer Protection Act (TCPA) and the associated...</p><a>Read More »</a></div></div>
  </div>
</section>

<section class="features">
  <h2 class="section-title">System Features</h2>
  <div class="feature-row">
    <div class="feature f1" role="img" aria-label="Illustration of a desktop computer showing on-screen notifications"><div class="caption">Notification System <svg width="12" height="12" viewBox="0 0 12 12"><circle cx="6" cy="6" r="5.5" fill="#fff"/><path d="M5 3.5L7.5 6 5 8.5" stroke="#5a9864" stroke-width="1.5" fill="none"/></svg></div></div>
    <div class="feature f2" role="img" aria-label="Illustration of call center agents with headsets and speech bubbles"><div class="caption">Agent Ranking <svg width="12" height="12" viewBox="0 0 12 12"><circle cx="6" cy="6" r="5.5" fill="#fff"/><path d="M5 3.5L7.5 6 5 8.5" stroke="#5a9864" stroke-width="1.5" fill="none"/></svg></div></div>
    <div class="feature f3" role="img" aria-label="Illustration of a hand holding a smartphone during a call"><div class="caption">Top Missed Points <svg width="12" height="12" viewBox="0 0 12 12"><circle cx="6" cy="6" r="5.5" fill="#fff"/><path d="M5 3.5L7.5 6 5 8.5" stroke="#3f8a9b" stroke-width="1.5" fill="none"/></svg></div></div>
    <div class="feature f4" role="img" aria-label="Illustration of a laptop on a desk with a video player, coffee and phone"><div class="caption">Transcribe and Redact <svg width="12" height="12" viewBox="0 0 12 12"><circle cx="6" cy="6" r="5.5" fill="#fff"/><path d="M5 3.5L7.5 6 5 8.5" stroke="#1faa83" stroke-width="1.5" fill="none"/></svg></div></div>
  </div>
  <div class="feature-actions">
    <a class="btn alt">SYSTEMS DETAILS <svg width="11" height="11" viewBox="0 0 12 12"><circle cx="6" cy="6" r="5.5" fill="#fff"/><path d="M5 3.5L7.5 6 5 8.5" stroke="#0792cd" stroke-width="1.5" fill="none"/></svg></a>
    <a class="btn">SYSTEMS FEATURES <svg width="11" height="11" viewBox="0 0 12 12"><circle cx="6" cy="6" r="5.5" fill="#fff"/><path d="M5 3.5L7.5 6 5 8.5" stroke="#0255a3" stroke-width="1.5" fill="none"/></svg></a>
  </div>
</section>

<section class="team">
  <h2 class="section-title">The Team</h2>
  <p class="team-intro">Tallymark's outstanding cast of team members are relentless in their pursuit of perfection. They realize that quality means everything to their customers, and their customers mean everything to them. You can count on their motivated team of professionals to work tirelessly for you, and with decades of combined experience in the customer service and call quality industries, you can confidently know they have the capacity and wherewithal to do just that.</p>
  <svg class="arrow" style="left:138px" width="22" height="80" viewBox="0 0 22 80"><path d="M20 2L3 40l17 38" fill="none" stroke="#85cae6" stroke-width="2"/></svg>
  <svg class="arrow" style="left:1042px" width="22" height="80" viewBox="0 0 22 80"><path d="M2 2l17 38L2 78" fill="none" stroke="#85cae6" stroke-width="2"/></svg>
  <div class="member" style="left:213px"><div class="avatar" role="img" aria-label="Cartoon character portrait of team member"></div><h4>Evan Harlow</h4><span>CEO</span></div>
  <div class="member" style="left:407px"><div class="avatar" role="img" aria-label="Cartoon character portrait of team member"></div><h4>Lena Okafor</h4><span>Operation Manager</span></div>
  <div class="member" style="left:596px"><div class="avatar" role="img" aria-label="Cartoon character portrait of team member"></div><h4>Tobias Lind</h4><span>Vp of Client Services</span></div>
  <div class="member" style="left:790px"><div class="avatar" role="img" aria-label="Cartoon character portrait of team member"></div><h4>Mara Quell</h4><span>Training Manager</span></div>
</section>

<section class="press" aria-label="As featured in">
  <div class="press-row one"><span>Halvorn</span><span>Quillstone</span><span>Ferrow</span><span>Ledgerline</span><span>Marrowby</span><span>Ostrel</span><span>Penwick</span><span>Ashcombe</span></div>
  <div class="press-row two"><span>Brisk Works</span><span>Cogbyte</span><span>Adhaven</span><span>Pitchline</span><span>Startwell</span><span>Clatterly</span><span>Foundry</span><span>Lantern</span></div>
</section>

<section class="testimonial">
  <div class="avatar" role="img" aria-label="Cartoon character portrait of client"></div>
  <blockquote>“ Tallymark has opened up a whole new world of measurement for our staff. Their team has been personable, flexible, and focused on improving our bottom line in a way that has made us feel valued as a top priority. We look forward to continuing to work with them on new innovations that can improve both customer and employee satisfaction!</blockquote>
  <div class="who">OWEN CASTELL</div>
  <div class="org">Brightway Mutual</div>
  <div class="dots"><i class="on"></i><i></i><i></i></div>
</section>

<footer class="site-footer">
  <a class="brand"><span class="dot"></span>Tallymark</a>
  <div class="footer-col" style="left:421px"><h5>Company</h5><ul><li>Home</li><li>Who We Are</li><li>Services</li><li>Blog</li><li>Login</li></ul></div>
  <div class="footer-col" style="left:582px"><h5>Contact Details</h5><ul>
    <li><svg width="10" height="13" viewBox="0 0 12 16"><path d="M6 0a6 6 0 0 0-6 6c0 4.5 6 10 6 10s6-5.5 6-10a6 6 0 0 0-6-6zm0 8.5A2.5 2.5 0 1 1 6 3.5a2.5 2.5 0 0 1 0 5z" fill="#555"/></svg>4810 Orchard Row</li>
    <li style="padding-left:18px">Maple Glen, CA 90000</li>
    <li>EMAIL: hello@tallymark.com</li>
    <li><svg width="10" height="10" viewBox="0 0 24 24"><path fill="#555" d="M6.6 10.8a15 15 0 0 0 6.6 6.6l2.2-2.2c.3-.3.7-.4 1-.2 1.1.4 2.3.6 3.6.6.6 0 1 .4 1 1V20c0 .6-.4 1-1 1A17 17 0 0 1 3 4c0-.6.4-1 1-1h3.5c.6 0 1 .4 1 1 0 1.3.2 2.5.6 3.6.1.3 0 .7-.2 1z"/></svg>PHONE: 555.014.2260</li></ul></div>
  <div class="footer-col newsletter" style="left:852px"><h5>Newsletter</h5><input type="email" placeholder="Enter Email Address"><a class="btn">SUBSCRIBE</a></div>
</footer>

<div class="copyright">
  <span class="left">Copyrights © 2017 , tallymark | All rights reserved.</span>
  <span class="right">Connect With Us : <i></i><i></i><i></i><i></i></span>
</div>

</body>
</html>
```